Winter is coming, is your home ready ?

We are a full service Insulation contracting services company . We insulate new and existing homes, commercial and industrial buildings.

We are looking for a billboard that shows our harsh winter approaching and a call to action for getting a free estimate.

We specialize in spray foam insulation but it doesn't need to be called out on the billboard if too much text make it looks too busy.

We do enjoy humor if its something that could work and keep people thinking of us.
Company web site is www.brambowinsulation.com
Company phone number is 555-318-2947

```html
<!DOCTYPE html>
<html lang="en">
<head>
<meta charset="utf-8">
<title>Brambow Insulation Billboard</title>
<link rel="stylesheet" href="https://fonts.googleapis.com/css2?family=Exo+2:wght@300;400;500;600;700;800&display=swap">
<style>
  :root {
    --page-bg: #e6ebef;
    --board-bg: #ffffff;
    --brand-green: #a5b91e;
    --text-gray: #5a5a5c;
    --text-dark: #4a4a4c;
    --rule-gray: #6a6a6a;
    --photo-dark: #4a3526;
    --photo-mid: #8c8f94;
    --photo-light: #e9ecef;
    --accent-triangle: #6b6b6d;
  }
  * { margin: 0; padding: 0; box-sizing: border-box; }
  html, body {
    width: 1200px; height: 780px; overflow: hidden;
    background: var(--page-bg);
    font-family: "Exo 2", sans-serif;
  }
  .billboard {
    position: absolute; left: 20px; top: 187px;
    width: 1160px; height: 405px;
    background: var(--board-bg);
    overflow: hidden;
  }
  .winter-photo { position: absolute; left: 0; top: 0; width: 620px; height: 405px; }
  .brand {
    position: absolute; left: 20px; top: 16px;
    display: flex; align-items: flex-start; gap: 6px;
    color: var(--text-gray); font-weight: 500;
  }
  .brand-mark { width: 14px; height: 14px; background: var(--brand-green); margin-top: 8px; }
  .brand-name { font-size: 32px; line-height: 1; letter-spacing: 0.5px; }
  .brand-sub { font-size: 11px; letter-spacing: 4.5px; margin-top: 3px; display: block; }
  .specialty-band {
    position: absolute; left: 0; top: 312px; width: 600px; height: 56px;
    background: rgba(255,255,255,0.55);
  }
  .specialty-text {
    position: absolute; left: 32px; top: 322px;
    font-size: 29px; font-weight: 300; color: var(--text-gray); white-space: nowrap;
  }
  .specialty-text strong { font-weight: 700; }
  .headline {
    position: absolute; left: 590px; width: 490px; text-align: center;
  }
  .headline-top {
    top: 18px; font-size: 47px; font-weight: 300; color: var(--text-gray);
    letter-spacing: -0.5px;
  }
  .headline-main {
    top: 76px; left: 560px; width: 550px;
    font-size: 58px; font-weight: 800; color: var(--brand-green); letter-spacing: -0.5px;
  }
  .services {
    position: absolute; left: 601px; top: 159px; width: 466px; height: 44px;
    border-top: 2px solid var(--rule-gray); border-bottom: 2px solid var(--rule-gray);
    text-align: center; font-size: 27px; font-weight: 600; line-height: 40px;
    color: var(--brand-green);
  }
  .services .divider { color: var(--text-dark); font-weight: 500; }
  .cta-band {
    position: absolute; left: 519px; top: 228px; width: 641px; height: 52px;
    background: var(--brand-green); color: #fff;
    font-size: 32px; font-weight: 300; line-height: 52px; padding-left: 37px;
    white-space: nowrap;
  }
  .cta-band strong { font-weight: 700; }
  .contact {
    position: absolute; left: 664px; display: flex; align-items: center; gap: 11px;
    color: var(--text-dark); white-space: nowrap;
  }
  .contact-phone { top: 292px; font-size: 55px; font-weight: 700; }
  .contact-web { top: 350px; font-size: 29px; font-weight: 500; }
  .contact-icon { flex: none; }
</style>
</head>
<body>
  <main class="billboard">
    <svg class="winter-photo" viewBox="0 0 620 405" role="img" aria-label="Photo of a snow-covered wooden house with a steep thatched roof in falling snow">
      <defs>
        <linearGradient id="photoTone" x1="0" y1="0" x2="0.6" y2="1">
          <stop offset="0" stop-color="var(--photo-light)"/>
          <stop offset="0.35" stop-color="var(--photo-mid)"/>
          <stop offset="0.7" stop-color="var(--photo-dark)"/>
          <stop offset="1" stop-color="var(--photo-light)"/>
        </linearGradient>
      </defs>
      <polygon points="0,0 441,0 619,405 0,405" fill="url(#photoTone)"/>
      <polygon points="447,0 486,0 475,59" fill="var(--accent-triangle)"/>
    </svg>

    <div class="brand">
      <span class="brand-mark"></span>
      <div>
        <span class="brand-name">brambow</span>
        <span class="brand-sub">insulation, inc.</span>
      </div>
    </div>

    <div class="specialty-band"></div>
    <p class="specialty-text">We <strong>specialize</strong> in spray foam insulation</p>

    <h1 class="headline headline-top">Winter is coming,</h1>
    <h2 class="headline headline-main">is your home ready?</h2>

    <p class="services">Residential <span class="divider">|</span> Commercial <span class="divider">|</span> Industrial</p>

    <p class="cta-band">CALL FOR GETTING A <strong>FREE ESTIMATE</strong></p>

    <p class="contact contact-phone">
      <svg class="contact-icon" width="48" height="48" viewBox="0 0 48 48" aria-hidden="true">
        <circle cx="24" cy="24" r="22" fill="none" stroke="var(--brand-green)" stroke-width="2.5"/>
        <path d="M17 14c-2 1-3 3-2 6 2 6 7 12 13 14 3 1 5 0 6-2l-4-4-3 2c-3-1-6-4-7-7l2-3z" fill="var(--text-dark)"/>
        <path d="M27 14a8 8 0 0 1 7 7M27 10a12 12 0 0 1 11 11" fill="none" stroke="var(--text-dark)" stroke-width="2"/>
      </svg>
      555-318-2947
    </p>
    <p class="contact contact-web">
      <svg class="contact-icon" width="48" height="48" viewBox="0 0 48 48" aria-hidden="true">
        <circle cx="24" cy="24" r="22" fill="none" stroke="var(--brand-green)" stroke-width="2.5"/>
        <circle cx="24" cy="24" r="13" fill="none" stroke="var(--text-dark)" stroke-width="2"/>
        <ellipse cx="24" cy="24" rx="6" ry="13" fill="none" stroke="var(--text-dark)" stroke-width="2"/>
        <path d="M11 24h26M13 17h22M13 31h22" stroke="var(--text-dark)" stroke-width="2"/>
      </svg>
      www.brambowinsulation.com
    </p>
  </main>
</body>
</html>
```